International IT business needs website revamp.

Velmor Limited would like their current website (www.velmorlimited-example.com) to be revamped/modernized to reflect up-to-date goods and services. Currently, Velmor is offering a conversational AI workflow platform for both enterprise clients and as a DIY solution for SMBs. This platform is called tqFlowbin and allows organizations to automate simple and repetitive workflows to drive their operational efficiency. In addition to the solution offering, Velmor Limited also provides professional IT services. With that said, please use www.velmorlimited-example.com and www.tqflowbin-example.ai for reference of current logos and colourways desired. Furthermore, refer to the attached PDF for a general idea of what to include in the site. The final design should be easy to navigate, clear, concise, and emphasize tqFlowbin as a solution for enterprise clients (while redirecting SMBs to the tqFlowbin website) looking to automate workflow processes/kickstart their digital transformation journey.

```html
<!DOCTYPE html>
<html lang="en">
<head>
<meta charset="utf-8">
<title>Velmor Limited — Enterprise Workflow Automation</title>
<link href="https://fonts.googleapis.com/css2?family=Poppins:wght@400;500;600;700;800&display=swap" rel="stylesheet">
<style>
:root{
  --ink:#111111;
  --text:#444a52;
  --blue:#0a8fd6;
  --blue-dark:#0a5fb0;
  --blue-light:#19b6ec;
  --pale:#eef8fd;
  --pale-2:#e4f4fb;
  --line:#5aaee0;
  --star:#f5a623;
  --white:#ffffff;
  --rule:#e3e7ea;
}
*{margin:0;padding:0;box-sizing:border-box}
html,body{width:1200px;height:2875px;overflow:hidden;background:var(--white)}
body{font-family:"Poppins",sans-serif;color:var(--ink);position:relative}
.abs{position:absolute}
.center{text-align:center}

/* header */
.site-header{position:absolute;left:0;top:0;width:1200px;height:94px;background:var(--white)}
.brand{position:absolute;display:flex;align-items:center;gap:6px;font-weight:500;color:var(--ink);letter-spacing:.5px}
.brand .mark{display:block;border:3px solid var(--ink)}
.site-header .brand{left:235px;top:28px;font-size:28px}
.site-header .brand .mark{width:38px;height:38px}
.main-nav{position:absolute;left:414px;top:33px;display:flex;gap:22px;align-items:center;font-size:10.5px;font-weight:500;letter-spacing:.3px}
.main-nav a{color:var(--ink);text-decoration:none;padding:7px 0}
.main-nav a.active{border:1.5px solid var(--ink);padding:6px 13px}
.header-phone{position:absolute;left:816px;top:34px;font-size:16px;font-weight:500;display:flex;align-items:center;gap:9px}

/* hero */
.hero{position:absolute;left:0;top:94px;width:1200px;height:470px}
.hero-title{position:absolute;top:44px;width:100%;text-align:center;font-size:33px;font-weight:600;letter-spacing:1.5px}
.product-name{position:absolute;left:504px;top:125px;display:flex;align-items:center;gap:10px;font-size:30px;font-weight:400;color:var(--blue)}
.product-name .dot{width:34px;height:34px;border-radius:50%;background:var(--blue)}
.slider-arrow{position:absolute;top:194px;width:34px;height:34px;border:2px solid var(--ink)}
.feature-label{position:absolute;top:346px;width:220px;text-align:center;font-size:13px;font-weight:600}
.slider-dots{position:absolute;top:408px;left:574px;display:flex;gap:7px}
.slider-dots span{width:12px;height:12px;border:1.5px solid var(--ink)}
.slider-dots span.on{background:var(--ink)}

/* section headings */
.eyebrow{position:absolute;width:100%;text-align:center;font-size:12px;font-weight:600;letter-spacing:3px;color:var(--blue)}
.section-title{position:absolute;width:100%;text-align:center;font-size:32px;font-weight:700}

/* services */
.services-intro{position:absolute;left:284px;top:712px;width:632px;text-align:center;font-size:9.6px;line-height:15px;color:var(--text)}
.service-card{position:absolute;top:834px;width:226px;height:256px}
.service-card .body{position:absolute;left:0;top:0;width:100%;height:100%;padding:0 30px}
.service-card .icon{position:absolute;left:86px;top:34px;width:54px;height:54px;border-radius:50%;background:linear-gradient(135deg,var(--blue-light),var(--blue-dark))}
.service-card h3{position:absolute;left:34px;top:110px;font-size:13px;font-weight:600;color:#2b2f33;width:180px}
.service-card ul{position:absolute;left:34px;top:140px;width:170px;list-style:none;font-size:9px;line-height:15px;color:var(--text)}
.service-card li{position:relative;padding-left:11px;margin-bottom:4px}
.service-card li::before{content:"";position:absolute;left:0;top:5px;width:4px;height:4px;border-radius:50%;background:var(--blue)}
.center-mark{position:absolute;left:546px;top:908px;width:108px;height:108px;background:linear-gradient(135deg,var(--blue-light),var(--blue-dark))}

/* testimonials */
.testimonials{position:absolute;left:0;top:1161px;width:1200px;height:545px;background:var(--pale)}
.quote-card{position:absolute;top:161px;width:356px;height:292px;background:var(--white);box-shadow:0 2px 10px rgba(10,70,120,.08);padding:18px 28px}
.quote-card .qmark{font-size:64px;line-height:56px;font-weight:700;color:var(--blue);height:44px}
.quote-card p{font-size:10.2px;line-height:16.3px;color:var(--text)}
.quote-card .who{margin-top:13px;font-size:11.5px;font-weight:600;color:#2b2f33}
.quote-card .stars{margin-top:2px;font-size:14px;color:var(--star);letter-spacing:1px}
.pager{position:absolute;top:500px;left:582px;display:flex;gap:5px}
.pager span{width:5px;height:5px;border-radius:50%;background:#9aa4ad}
.pager span.on{background:var(--blue)}

/* video */
.video-frame{position:absolute;left:234px;top:1771px;width:731px;height:414px;background:linear-gradient(110deg,#62c6ec 0%,#2b97d8 45%,#0b5fae 100%)}
.play{position:absolute;left:320px;top:161px;width:92px;height:92px}

/* clients & partners */
.divider{position:absolute;left:600px;top:2185px;width:1px;height:292px;background:var(--rule)}
.logo-group{position:absolute;top:2244px;width:300px}
.logo-group h2{text-align:center;font-size:25px;font-weight:700}
.logo-row{display:flex;justify-content:center;gap:28px;align-items:center;height:58px}
.logo-row:first-of-type{margin-top:22px}
.logo-name{font-size:27px;font-weight:700}
.ln-north{color:#1a5aa8}
.ln-pay{color:#5b5f97}
.ln-orbix{color:#1d1d1d}
.ln-road{color:#c8202f;font-size:19px}
.to-top{position:absolute;left:583px;top:2477px;width:34px;height:34px;border-radius:50%;background:linear-gradient(135deg,var(--blue-light),var(--blue-dark))}

/* footer */
.site-footer{position:absolute;left:0;top:2500px;width:1200px;height:375px}
.site-footer .brand{left:234px;top:102px;font-size:17px}
.site-footer .brand .mark{width:24px;height:24px;border-width:2px}
.footer-about{position:absolute;left:234px;top:140px;width:240px;font-size:9.2px;line-height:15px;color:#2b2f33}
.footer-col{position:absolute;top:96px}
.footer-col h4{font-size:11px;font-weight:600;letter-spacing:.3px}
.footer-col h4::after{content:"";display:block;width:28px;height:2px;background:var(--blue);margin-top:9px}
.footer-col ul{list-style:none;margin-top:16px;font-size:9.2px;line-height:15px;color:#2b2f33}
.footer-col.links li{margin-bottom:10px}
.footer-col.contact li{margin-bottom:8px}
.footer-col.social li{display:flex;align-items:center;gap:8px;margin-bottom:8px}
.footer-col.social .bubble{width:17px;height:17px;border-radius:50%;background:linear-gradient(135deg,var(--blue-light),var(--blue-dark))}
.footer-rule{position:absolute;left:234px;top:307px;width:731px;height:1px;background:var(--rule)}
.copyright{position:absolute;top:338px;width:100%;text-align:center;font-size:9.2px;color:#2b2f33}
</style>
</head>
<body>

<header class="site-header">
  <div class="brand"><span class="mark"></span>VELMOR</div>
  <nav class="main-nav">
    <a class="active" href="#">HOME</a>
    <a href="#">SOLUTIONS</a>
    <a href="#">SERVICES</a>
    <a href="#">ABOUT US</a>
    <a href="#">CONTACT US</a>
  </nav>
  <div class="header-phone">
    <svg width="15" height="15" viewBox="0 0 24 24"><path fill="#0a8fd6" d="M6.6 10.8a15.1 15.1 0 0 0 6.6 6.6l2.2-2.2c.3-.3.7-.4 1-.2 1.1.4 2.3.6 3.6.6.6 0 1 .4 1 1V20c0 .6-.4 1-1 1C10.6 21 3 13.4 3 4c0-.6.4-1 1-1h3.5c.6 0 1 .4 1 1 0 1.3.2 2.5.6 3.6.1.3 0 .7-.2 1z"/></svg>
    (555) 014-2290
  </div>
</header>

<section class="hero">
  <svg class="abs" style="left:0;top:0" width="1200" height="470" viewBox="0 0 1200 470">
    <path d="M0 0H1200V397L600 470 0 397Z" fill="#eaf7fd"/>
    <g fill="none" stroke="#5aaee0" stroke-width="1.2" stroke-dasharray="4 4">
      <path d="M600 72V110"/>
      <path d="M600 186V238"/>
      <path d="M575 190V197Q575 205 567 205H368V238"/>
      <path d="M625 190V197Q625 205 633 205H832V238"/>
      <circle cx="369" cy="287" r="47"/>
      <circle cx="600" cy="287" r="47"/>
      <circle cx="834" cy="287" r="47"/>
    </g>
    <g fill="none" stroke="#0a8fd6" stroke-width="1.6">
      <rect x="346" y="272" width="30" height="22" rx="2"/>
      <rect x="366" y="264" width="28" height="20" rx="2"/>
      <circle cx="361" cy="283" r="6"/>
      <path d="M372 270h16M372 276h16"/>
      <rect x="585" y="262" width="28" height="38" rx="2"/>
      <path d="M591 272h16M591 279h16M591 286h10"/>
      <rect x="820" y="262" width="28" height="46" rx="4"/>
      <path d="M826 298v-8M832 298v-13M838 298v-18M844 298v-22"/>
    </g>
  </svg>
  <h1 class="hero-title">ENTERPRISE CLIENT</h1>
  <div class="product-name"><span class="dot"></span>tqFlowbin</div>
  <svg class="slider-arrow" style="left:200px" viewBox="0 0 34 34"><path d="M19 10l-7 7 7 7" fill="none" stroke="#111" stroke-width="2"/></svg>
  <svg class="slider-arrow" style="left:966px" viewBox="0 0 34 34"><path d="M15 10l7 7-7 7" fill="none" stroke="#111" stroke-width="2"/></svg>
  <div class="feature-label" style="left:259px">80/20 Automation</div>
  <div class="feature-label" style="left:490px">Customer Experience</div>
  <div class="feature-label" style="left:724px">Call Volume Agnostic</div>
  <div class="slider-dots"><span class="on"></span><span></span><span></span></div>
</section>

<section class="services">
  <div class="eyebrow" style="top:636px">SERVICES</div>
  <h2 class="section-title" style="top:660px">What We Do</h2>
  <p class="services-intro">Contract Staffing: At Velmor, our staff are readily available to deliver experienced and knowledgeable assistance to fill immediate or temporary needs for a diverse range of technologies and positions. Thus, we provide seasoned IT resources with a strong sense of business acumen to bring valuable experience and expertise to our clients to achieve reduced costs, greater efficiency and better services.</p>
  <svg class="abs" style="left:0;top:776px" width="1200" height="60" viewBox="0 0 1200 60">
    <g fill="none" stroke="#9fb4c2" stroke-width="1" stroke-dasharray="4 4">
      <path d="M575 0V8Q575 26 560 26H368V58"/>
      <path d="M625 0V8Q625 26 640 26H832V58"/>
    </g>
  </svg>
  <article class="service-card" style="left:254px">
    <svg class="abs" style="left:0;top:0" width="226" height="256" viewBox="0 0 226 256"><path d="M113 0L222 60Q226 62 226 67V189Q226 194 222 196L113 256 4 196Q0 194 0 189V67Q0 62 4 60Z" fill="#eaf7fd"/></svg>
    <span class="icon"></span>
    <h3>Digital Transformation</h3>
    <ul><li>Process Automation via RPA and Conversational AI</li><li>Enterprise Application Integration</li></ul>
  </article>
  <div class="center-mark"></div>
  <article class="service-card" style="left:720px">
    <svg class="abs" style="left:0;top:0" width="226" height="256" viewBox="0 0 226 256"><path d="M113 0L222 60Q226 62 226 67V189Q226 194 222 196L113 256 4 196Q0 194 0 189V67Q0 62 4 60Z" fill="#eaf7fd"/></svg>
    <span class="icon"></span>
    <h3 style="left:42px">Network of Expertise</h3>
    <ul style="left:34px"><li>full-stack development,</li><li>from AI/ML, and data to legacy</li></ul>
  </article>
</section>

<section class="testimonials">
  <div class="eyebrow" style="top:55px">TESTIMONIALS</div>
  <h2 class="section-title" style="top:79px">What Our Clients Are Saying</h2>
  <article class="quote-card" style="left:234px">
    <div class="qmark">“</div>
    <p>“Naturally, the Travel Docs Agency website receives thousands of visitors a day. As a result, we noticed the need to automate simple and repetitive questions to provide quick, on-demand assistance while maximizing our worker productivity without compromising costs. Thus, we enlisted Velmor Limited and their tqFlowbin solution to accomplish the task. Since launching the Travel Docs Agency bot in Q4, 2019, we have achieved over 75% of inquiries being automatically answered successfully!”</p>
    <div class="who">Travel Docs Agency</div>
    <div class="stars">★★★★★</div>
  </article>
  <article class="quote-card" style="left:609px">
    <div class="qmark">“</div>
    <p>“Leveraging tqFlowbin’s extremely user-friendly interface, Citizen Services Office was able to build and implement our own bot for the My Citizen Account (MCA) page without the assistance of Velmor developers. By removing the need for programmers, we are able to make adjustments to our bot instantaneously!”</p>
    <div class="who">Citizen Services Office</div>
    <div class="stars">★★★★★</div>
  </article>
  <div class="pager"><span class="on"></span><span></span><span></span><span></span></div>
</section>

<div class="video-frame" role="img" aria-label="Photo of a smiling woman working on a tablet, tinted blue">
  <svg class="play" viewBox="0 0 92 92"><circle cx="46" cy="46" r="44" fill="none" stroke="#fff" stroke-width="3"/><path d="M37 30L63 46 37 62Z" fill="#fff"/></svg>
</div>

<div class="divider"></div>
<section class="logo-group" style="left:262px">
  <h2>Our Clients</h2>
  <div class="logo-row"><span class="logo-name ln-north">Northline</span><span class="logo-name ln-pay" style="font-size:21px">Paylane</span></div>
  <div class="logo-row"><span class="logo-name ln-orbix">Orbix</span><span class="logo-name ln-road">Roadway Club</span></div>
</section>
<section class="logo-group" style="left:638px">
  <h2>Our Partners</h2>
  <div class="logo-row"><span class="logo-name ln-north">Northline</span><span class="logo-name ln-pay" style="font-size:21px">Paylane</span></div>
  <div class="logo-row"><span class="logo-name ln-orbix">Orbix</span><span class="logo-name ln-road">Roadway Club</span></div>
</section>

<footer class="site-footer">
  <svg class="abs" style="left:0;top:0" width="1200" height="375" viewBox="0 0 1200 375"><path d="M0 62Q300 -10 600 40T1200 40V375H0Z" fill="#eef8fd"/></svg>
  <svg class="to-top" style="left:583px;top:-23px" viewBox="0 0 34 34"><path d="M12 19l5-5 5 5" fill="none" stroke="#fff" stroke-width="2"/></svg>
  <div class="brand"><span class="mark"></span>VELMOR</div>
  <p class="footer-about">Since 2011, the Velmor team has been providing professional IT services for major Canadian corporations operating in the telecommunications and financial sectors. As such, our team is highly skilled in technology integration, legacy modernization, system architecture design, application development, quality assurance, project management and more!</p>
  <div class="footer-col links" style="left:502px">
    <h4>QUICK LINKS</h4>
    <ul><li>Home</li><li>Solutions</li><li>Services</li><li>About Us</li><li>Contact Us</li></ul>
  </div>
  <div class="footer-col contact" style="left:618px">
    <h4>CONTACT US</h4>
    <ul><li>1200 Example Avenue, Unit 5, Springfield,<br>ON Canada, A1B 2C3</li><li>Phone: (555) 014-2290</li><li>Email: info@velmorlimited-example.com</li></ul>
  </div>
  <div class="footer-col social" style="left:840px">
    <h4>FOLLOW US</h4>
    <ul><li><span class="bubble"></span>Friendspace</li><li><span class="bubble"></span>Chirper</li><li><span class="bubble"></span>Workedin</li></ul>
  </div>
  <div class="footer-rule"></div>
  <div class="copyright">Copyrights © 2020 Velmor Limited. All rights reserved</div>
</footer>

</body>
</html>
```